automotive repair and collision repair shop card

our company is called K.L Motor service we are a automotive repair company
we also do government inspections. the company information is on the cards. I would like you to use my new logo and create a new card and use the information from my old card. Good Luck!!

Industry/Entity Type

Car Repair

Contact Information for Business Card

Address: #417-18842 52 Ave, Surrey, BC V5K 8R3
Phone:(604) 555-0187
fax 604 555 0193
website www.klmotorworks.example

Font styles to use
Serif
Sans Serif

Requirements
Must have
• all the information
Should not have
• the owner and there name

```html
<!DOCTYPE html>
<html lang="en">
<head>
<meta charset="utf-8">
<title>K.L Motor service – Business Card</title>
<link rel="stylesheet" href="https://fonts.googleapis.com/css2?family=Open+Sans:wght@400;600&display=swap">
<style>
  :root {
    --bg: #e9e7e3;
    --card: #ffffff;
    --ink: #1d1d1d;
    --band: #141414;
    --band-edge: #3a3a3a;
    --rule: #9a9a9a;
    --muted: #555555;
    --on-band: #e6e6e6;
  }
  * { box-sizing: border-box; margin: 0; padding: 0; }
  html, body { width: 1200px; height: 900px; overflow: hidden; }
  body {
    background: var(--bg);
    font-family: "Open Sans", Arial, sans-serif;
    color: var(--ink);
    display: flex;
    flex-direction: column;
    align-items: center;
    justify-content: center;
    gap: 60px;
  }
  .card {
    position: relative;
    width: 630px;
    height: 360px;
    background: var(--card);
    border-radius: 18px;
    overflow: hidden;
    box-shadow: 0 6px 18px rgba(0,0,0,0.18);
  }
  .card__bands { position: absolute; inset: 0; width: 100%; height: 100%; }
  .brand {
    position: absolute;
    display: flex;
    align-items: center;
    gap: 14px;
  }
  .brand__mark {
    width: 22px; height: 22px;
    border-radius: 50%;
    background: var(--ink);
    flex: none;
  }
  .brand__text { display: flex; flex-direction: column; }
  .brand__name {
    font-weight: 600;
    font-size: 36px;
    line-height: 1.05;
    color: var(--ink);
    letter-spacing: 0.5px;
  }
  .brand__tagline {
    font-size: 13px;
    color: var(--muted);
    align-self: flex-end;
    margin-top: 4px;
  }
  .card--front .brand { left: 50%; top: 112px; transform: translateX(-50%); }

  .card--back .brand { left: 300px; top: 110px; }
  .card--back .brand__name { font-size: 27px; }
  .card--back .brand__mark { width: 18px; height: 18px; }
  .divider {
    position: absolute;
    left: 272px; top: 68px;
    width: 1px; height: 150px;
    background: linear-gradient(to bottom, transparent, var(--rule) 20%, var(--rule) 80%, transparent);
    transform: rotate(-10deg);
  }
  .contact {
    position: absolute;
    left: 46px; top: 104px;
    list-style: none;
    font-size: 13.5px;
    line-height: 1;
  }
  .contact__item { display: flex; align-items: center; gap: 12px; height: 23px; }
  .contact__icon { width: 16px; height: 16px; flex: none; fill: none; stroke: var(--ink); stroke-width: 1.6; }
  .contact__icon--solid { fill: var(--ink); stroke: none; }
  .address {
    position: absolute;
    left: 0; right: 0; bottom: 30px;
    text-align: center;
    font-size: 14px;
    letter-spacing: 0.3px;
    color: var(--on-band);
  }
</style>
</head>
<body>

  <section class="card card--front" aria-label="Business card front">
    <svg class="card__bands" viewBox="0 0 630 360" preserveAspectRatio="none" aria-hidden="true">
      <path d="M0,0 H630 V6 Q320,14 0,34 Z" fill="var(--band)"/>
      <path d="M0,36 Q320,16 630,8" fill="none" stroke="var(--rule)" stroke-width="1.2"/>
      <path d="M0,312 Q300,250 630,228 V360 H0 Z" fill="var(--band)"/>
      <path d="M0,304 Q300,242 630,220" fill="none" stroke="var(--band-edge)" stroke-width="2"/>
    </svg>
    <div class="brand">
      <span class="brand__mark"></span>
      <div class="brand__text">
        <span class="brand__name">K.L Motor service</span>
        <span class="brand__tagline">One Stop Repair Shop</span>
      </div>
    </div>
  </section>

  <section class="card card--back" aria-label="Business card back">
    <svg class="card__bands" viewBox="0 0 630 360" preserveAspectRatio="none" aria-hidden="true">
      <path d="M0,300 Q300,232 630,212 V360 H0 Z" fill="var(--band)"/>
      <path d="M0,292 Q300,224 630,204" fill="none" stroke="var(--band-edge)" stroke-width="2"/>
    </svg>

    <ul class="contact">
      <li class="contact__item">
        <svg class="contact__icon contact__icon--solid" viewBox="0 0 16 16" aria-label="Fax"><rect x="4" y="1" width="8" height="5" rx="1"/><rect x="1" y="6" width="14" height="7" rx="2"/><rect x="4" y="11" width="8" height="4" fill="#fff"/></svg>
        <span>604 555 0193</span>
      </li>
      <li class="contact__item">
        <svg class="contact__icon contact__icon--solid" viewBox="0 0 16 16" aria-label="Phone"><path d="M4 1 L6 4 L4.6 5.6 Q6 9 10.4 11.4 L12 10 L15 12 L13 15 Q6 14 1 3 Z"/></svg>
        <span>(604) 555-0187</span>
      </li>
      <li class="contact__item">
        <svg class="contact__icon" viewBox="0 0 16 16" aria-label="Email"><rect x="1" y="3" width="14" height="10" rx="1"/><path d="M1 3 L8 9 L15 3"/></svg>
        <span>info@klmotorworks.example</span>
      </li>
      <li class="contact__item">
        <svg class="contact__icon" viewBox="0 0 16 16" aria-label="Website"><circle cx="8" cy="8" r="6.5"/><ellipse cx="8" cy="8" rx="3" ry="6.5"/><path d="M1.5 8 H14.5 M2.5 4.5 H13.5 M2.5 11.5 H13.5"/></svg>
        <span>www.klmotorworks.example</span>
      </li>
    </ul>

    <div class="divider"></div>

    <div class="brand">
      <span class="brand__mark"></span>
      <div class="brand__text">
        <span class="brand__name">K.L Motor service</span>
        <span class="brand__tagline">One Stop Repair Shop</span>
      </div>
    </div>

    <p class="address">#417-18842 52 Ave, Surrey, BC V5K 8R3</p>
  </section>

</body>
</html>
```